Letterhead That Inspires Trust

Harbor Deed Remedies, LLC, (HDR) fixes technical problems with property deeds. The problems usually surface when someone tries to buy, sell or mortgage a piece of real estate and one of the lawyers involved find a title defect (a lien, an undischarged mortgage, a deceased person still on the title, unpaid taxes, etc.). HDR then gets involved and often has to contact prior property owners to get them to sign paperwork fixing the problem. We need a letterhead that will a) convey the seriousness of what we are trying to do, b) cause the recipients of our letters to recognize the importance of what are trying to do, and c) convey that we are a established and trustworthy company. We want it to include an image that suggests we are a problem solving company. Attached is an image we think might work; you can use it or not. In addition to our name (Harbor Deed Remedies, LLC), the letterhead must include our address and phone number: 418 Alder Lane, Suite 207, Eastbrook, RI 02914 (401) 555-3827. We are thinking something straightforward without unnecessary colors or graphics.

```html
<!DOCTYPE html>
<html lang="en">
<head>
<meta charset="utf-8">
<title>Harbor Deed Remedies, LLC — Letterhead</title>
<link rel="stylesheet" href="https://fonts.googleapis.com/css2?family=Cinzel:wght@600&family=Questrial&display=swap">
<style>
  :root {
    --backdrop: #e4e4e4;
    --paper: #ffffff;
    --bar-grey: #5f5f5f;
    --bar-black: #000000;
    --heading: #555555;
    --text: #2b2b2b;
    --rule: #8a6f6f;
    --visual-light: #f3efe9;
    --visual-wood: #e3c8a6;
    --visual-green: #b9dca0;
  }
  * { margin: 0; padding: 0; box-sizing: border-box; }
  html, body { width: 1200px; height: 1200px; overflow: hidden; background: var(--backdrop); }
  .letterhead {
    position: absolute; left: 175px; top: 0; width: 849px; height: 1200px;
    background: var(--paper);
    font-family: "Questrial", sans-serif; color: var(--text);
  }
  .side-bar { position: absolute; left: 0; top: 0; width: 22px; height: 1200px; }
  .company-name {
    position: absolute; left: 75px; top: 80px;
    font-family: "Cinzel", serif; font-weight: 600; font-size: 32px; line-height: 36px;
    color: var(--heading); letter-spacing: 0.2px;
  }
  .contact {
    position: absolute; left: 574px; top: 85px; height: 61px;
    border-left: 1.5px solid var(--rule); padding-left: 12px;
    font-style: normal; font-size: 14.5px; line-height: 18px;
  }
  .contact .phone { margin-top: 11px; display: flex; align-items: center; gap: 4px; }
  .recipient { position: absolute; left: 80px; top: 335px; font-size: 16px; line-height: 23px; }
  .recipient { top: 336px; }
  .salutation { position: absolute; left: 80px; top: 497px; font-size: 16px; }
  .body-copy {
    position: absolute; left: 80px; top: 543px; width: 688px;
    font-size: 16px; line-height: 23px; text-align: justify; letter-spacing: 0.15px;
  }
  .signature {
    position: absolute; left: 75px; top: 935px; width: 320px; height: 80px;
    background: linear-gradient(90deg, #f1f1f1, #e6e6e6);
    border-radius: 4px;
  }
  .problem-solving-visual {
    position: absolute; left: 582px; top: 1047px; width: 219px; height: 118px;
    background: radial-gradient(ellipse at 55% 55%, var(--visual-green) 0%, var(--visual-wood) 35%, var(--visual-light) 75%, var(--paper) 100%);
  }
</style>
</head>
<body>
  <main class="letterhead">
    <svg class="side-bar" viewBox="0 0 22 1200" aria-hidden="true">
      <polygon points="0,0 22,0 22,833 0,820" fill="var(--bar-grey)"/>
      <polygon points="0,828 22,841 22,1200 0,1200" fill="var(--bar-black)"/>
    </svg>

    <h1 class="company-name">Harbor Deed<br>Remedies, LLC</h1>

    <address class="contact">
      <div>418 Alder Lane, Suite 207,</div>
      <div>Eastbrook, RI 02914</div>
      <div class="phone">
        <svg width="12" height="12" viewBox="0 0 24 24" aria-hidden="true"><path d="M6.6 10.8a15.1 15.1 0 0 0 6.6 6.6l2.2-2.2a1 1 0 0 1 1-.25 11.4 11.4 0 0 0 3.6.6 1 1 0 0 1 1 1V20a1 1 0 0 1-1 1A17 17 0 0 1 3 4a1 1 0 0 1 1-1h3.5a1 1 0 0 1 1 1c0 1.25.2 2.45.6 3.6a1 1 0 0 1-.25 1z" fill="var(--text)"/></svg>
        (401) 555-3827
      </div>
    </address>

    <div class="recipient">
      Mr. Samuel Reed<br>President<br>Meridian Ledger Partners<br>111 Street Name,<br>City State, 12345
    </div>

    <p class="salutation">Dear</p>

    <div class="body-copy">
      <p>Lorem ipsum dolor sit amet, consectetur adipiscing elit. Aenean ut ipsum eget massa hendrerit vestibulum vel in velit. Donec pretium neque velit.</p>
      <p>Aliquam porta lectus nec mauris ornare venenatis. Vivamus non est turpis, et cursus sem. Mauris vehicula erat in diam auctor at bibendum nisl lacinia.</p>
      <p>Morbi imperdiet neque vehicula nunc convallis gravida. Vestibulum iaculis pretium placerat. Integer consequat, est sit amet facilisis eleifend, nibh nibh varius orci, eget dapibus arcu dui non purus. Pellentesque in magna mauris. Duis enim sapien, dictum vitae condimentum a, pulvinar vel lacus. Mauris et molestie nibh. Vestibulum vitae nulla at metus elementum porta sit amet interdum elit. Nulla sollicitudin neque eu nulla volutpat congue.</p>
      <p>Etiam pellentesque, velit id dapibus fermentum, turpis sapien ornare dui, ac tincidunt ligula odio congue purus. Nunc sed ante dui, in porta lectus. Cras nec sem lorem. In hac habitasse platea dictumst. Maecenas id diam quis dui porta tristique. Sed id egestas felis. Donec ullamcorper mattis posuere. Phasellus fermentum eleifend tortor vel dapibus. Vestibulum ante ipsum.</p>
    </div>

    <div class="signature" role="img" aria-label="Handwritten signature of the sender"></div>

    <div class="problem-solving-visual" role="img" aria-label="Photo of wooden figures in groups linked by green lines to one green figure at the center, suggesting problem solving"></div>
  </main>
</body>
</html>
```